Media Services Start-up -- Corporate Website and Logo Design. Inspiration required!

We need a logo design and corporate website design, including coding, for our start-up business.
Vennatra’s value proposition is based on bringing together media content from a vast number of geographies globally, adding human and AI curation, translation and editing, and delivering the content using tailored customer interfaces. On the one hand, the business brings together media coverage from all over the world, and on the other it brings together content, human skills and technology to deliver a supreme customer experience.
Vennatra is a B2B media monitoring and analytics business with emphasis on global customers. Vennatra's service offering is centred around sourcing media content from different markets, processing, storing and delivering the content and insights derived from it using an online platform / mobile app.
The messaging we want to create through the logo is:
- Global scope
- Speed of delivery
- Cost-efficiency
- Multi-lingual
- Tailor-made
- Trustworthy
Target Market(s)
Business to business, PR / Communications, Media, Marketing
Logo Text
Vennatra
Coding
Coded - Design and coding required
Number of Pages Required
5+ page
Font styles to use
Other font styles liked:
- See Design Brief for details
Colors
Designer to choose colors to be used in the design.

```html
<!DOCTYPE html>
<html lang="en">
<head>
<meta charset="utf-8">
<title>Vennatra — How We Do It</title>
<link href="https://fonts.googleapis.com/css2?family=Roboto:wght@400;500;700&display=swap" rel="stylesheet">
<style>
:root{
  --teal:#3bb3a1;
  --header:#1c1c1c;
  --band:rgba(58,58,58,.88);
  --band-dark:rgba(30,30,30,.94);
  --text:#f2f2f2;
  --muted:#d8d8d8;
}
*{margin:0;padding:0;box-sizing:border-box}
html,body{width:1200px;height:839px;overflow:hidden;background:#000}
body{font-family:'Roboto',sans-serif;color:var(--text);position:relative}
.site-header{position:absolute;left:0;top:0;width:1200px;height:85px;background:var(--header);z-index:3}
.brand{position:absolute;left:140px;top:14px;font-size:48px;font-weight:700;color:#dcdcdc;letter-spacing:-.5px}
.contact{position:absolute;top:11px;display:flex;align-items:center;gap:8px;font-size:14px;color:var(--text)}
.contact svg{width:28px;height:28px}
.contact.phone{left:733px}
.contact.mail{left:899px}
.main-nav{position:absolute;top:53px;left:498px;display:flex;gap:26px;font-size:14.5px}
.main-nav a{color:var(--text);text-decoration:none}
.main-nav a.active{color:var(--teal);font-weight:500}
.sign-in{position:absolute;left:975px;top:49px;width:84px;height:28px;background:var(--teal);color:#fff;font-size:15px;display:flex;align-items:center;justify-content:center;letter-spacing:.3px}
.backdrop{position:absolute;left:0;top:85px;width:1200px;height:683px;
  background:radial-gradient(circle at 50% 45%,#4a4a4a 0,#2a2a2a 28%,#1c1c1c 60%),#1a1a1a}
.hero{position:absolute;top:85px;left:0;width:1200px;height:217px;text-align:center;z-index:2}
.hero h1{margin-top:54px;font-size:31px;font-weight:700}
.hero p{width:830px;margin:14px auto 0;font-size:13px;font-weight:500;line-height:22.5px}
.band{position:absolute;left:0;width:1200px;z-index:2}
.band .label{position:absolute;left:143px;font-size:21px;line-height:27px}
.sourcing{top:302px;height:141px;background:var(--band)}
.collection{top:450px;height:99px;background:var(--band-dark)}
.augmentation{top:560px;height:99px;background:var(--band-dark)}
.delivery{top:669px;height:99px;background:var(--band-dark)}
.source-item{position:absolute;top:18px;width:200px;margin-left:-100px;text-align:center;font-size:15px;line-height:20px}
.source-item svg{width:52px;height:52px;display:block;margin:0 auto 24px}
.item-text{position:absolute;font-size:15px;line-height:23.5px}
svg.icon{position:absolute;fill:none;stroke:#fff;stroke-width:1.6}
.end-strip{position:absolute;top:768px;left:0;width:1200px;height:37px;background:#000}
.site-footer{position:absolute;top:805px;left:0;width:1200px;height:34px;background:var(--teal);z-index:2}
.site-footer small{position:absolute;left:141px;top:9px;font-size:12.5px;color:#fff}
.social{position:absolute;right:141px;top:10px;display:flex;gap:10px}
.social span{width:14px;height:14px;border-radius:50%;background:#fff}
</style>
</head>
<body>
<header class="site-header">
  <div class="brand">Vennatra</div>
  <div class="contact phone">
    <svg viewBox="0 0 28 28"><circle cx="14" cy="14" r="12.5" fill="none" stroke="#3bb3a1" stroke-width="1.5"/><path d="M10 8.5l2.2 2.6-1.2 1.6c.8 1.8 2.2 3.2 4 4l1.6-1.2 2.6 2.2-1.2 1.8c-4.6-.4-8.7-4.5-9.2-9.2z" fill="#fff"/></svg>
    <span>+1 555 014 2290</span>
  </div>
  <div class="contact mail">
    <svg viewBox="0 0 28 28"><circle cx="14" cy="14" r="12.5" fill="none" stroke="#3bb3a1" stroke-width="1.5"/><rect x="8" y="10" width="12" height="8.5" fill="#fff"/><path d="M8 10l6 5 6-5" stroke="#1c1c1c" stroke-width="1.2" fill="none"/></svg>
    <span>hello@vennatra.example</span>
  </div>
  <nav class="main-nav">
    <a href="#">Home</a><a href="#">Solutions</a><a href="#" class="active">How We Do It</a><a href="#">Our People</a><a href="#">Our Technology</a>
  </nav>
  <a class="sign-in">SIGN IN</a>
</header>

<div class="backdrop" role="img" aria-label="Night city skyline with a person facing a glowing globe, linked by network lines to floating device icons"></div>

<section class="hero">
  <h1>How We Do It</h1>
  <p>We partner with in-market MMOs to source print, online, TV and radio content from 50+ geographies. Our multi-lingual analysts are domain experts with both in-depth market and industry expertise, and years of experience within media intelligence, PR and communications, and digital marketing.</p>
</section>

<section class="band sourcing">
  <div class="label" style="top:43px">Content<br>Sourcing</div>
  <div class="source-item" style="left:384px">
    <svg viewBox="0 0 52 52" fill="none" stroke="#fff" stroke-width="1.6"><rect x="3" y="2" width="38" height="48"/><path d="M41 8h6v42H3"/><rect x="8" y="7" width="28" height="8"/><path d="M8 20h14M8 25h14M8 30h14M8 35h28M8 40h28M8 45h28"/><rect x="25" y="20" width="11" height="11"/></svg>
    Print<br>Global MNO Partners
  </div>
  <div class="source-item" style="left:595px">
    <svg viewBox="0 0 52 52" fill="none" stroke="#fff" stroke-width="2"><rect x="4" y="28" width="20" height="10" rx="5" transform="rotate(-45 14 33)"/><rect x="28" y="14" width="20" height="10" rx="5" transform="rotate(-45 38 19)"/><path d="M19 33l14-14"/><path d="M2 30l4 1M6 24l3 3M40 46l-1-4M46 40l-3-3"/></svg>
    Online<br>Web Crawlers
  </div>
  <div class="source-item" style="left:794px">
    <svg viewBox="0 0 52 52" fill="none" stroke="#fff" stroke-width="1.6"><path d="M4 22v8M10 17v18M16 22v8M22 10v32M28 4v44M34 14v24M40 20v12M46 24v4"/></svg>
    Tv &amp; Radio<br>Aggregation
  </div>
  <div class="source-item" style="left:994px">
    <svg viewBox="0 0 52 52" fill="none" stroke="#fff" stroke-width="2.6"><circle cx="38" cy="10" r="7"/><circle cx="12" cy="26" r="7"/><circle cx="38" cy="42" r="7"/><path d="M18 22l14-8M18 30l14 8"/></svg>
    Social Media<br>Platform
  </div>
</section>

<section class="band collection">
  <div class="label" style="top:22px">Content<br>Collection</div>
  <svg class="icon" style="left:328px;top:26px" width="106" height="48" viewBox="0 0 106 48"><ellipse cx="20" cy="7" rx="20" ry="6"/><path d="M0 7v32c0 3.3 9 6 20 6s20-2.7 20-6V7M0 18c0 3.3 9 6 20 6s20-2.7 20-6M0 29c0 3.3 9 6 20 6s20-2.7 20-6"/><ellipse cx="62" cy="19" rx="14" ry="4.5"/><path d="M48 19v22c0 2.5 6.3 4.5 14 4.5s14-2 14-4.5V19M48 27c0 2.5 6.3 4.5 14 4.5S76 29.5 76 27M48 34c0 2.5 6.3 4.5 14 4.5S76 36.5 76 34"/><ellipse cx="94" cy="27" rx="11" ry="3.5"/><path d="M83 27v15c0 2 5 3.5 11 3.5s11-1.5 11-3.5V27M83 32c0 2 5 3.5 11 3.5s11-1.5 11-3.5M83 37c0 2 5 3.5 11 3.5s11-1.5 11-3.5"/></svg>
  <div class="item-text" style="left:458px;top:28px;line-height:20px">Content Repository<br>&amp; Archive</div>
</section>

<section class="band augmentation">
  <div class="label" style="top:22px">Content<br>Augmentation</div>
  <svg class="icon" style="left:328px;top:25px" width="50" height="50" viewBox="0 0 50 50"><circle cx="19" cy="19" r="11" stroke-dasharray="4 2.5"/><circle cx="19" cy="19" r="6"/><circle cx="19" cy="19" r="3"/><circle cx="37" cy="37" r="8" stroke-dasharray="3.5 2"/><circle cx="37" cy="37" r="3.5"/></svg>
  <div class="item-text" style="left:394px;top:15px">AI Content Enhancement<br>Validation &amp; Summarisation Tools<br>Delivery Customisation</div>
  <svg class="icon" style="left:707px;top:25px" width="56" height="50" viewBox="0 0 56 50"><path d="M2 48v-8c0-5 5-7 10-9v-4c-3-2-4-6-4-10 0-6 4-10 9-10s9 4 9 10c0 4-1 8-4 10v4c5 2 10 4 10 9v8z"/><path d="M26 6c2-2 5-3 8-3 5 0 9 4 9 10 0 4-1 8-4 10v4c5 2 10 4 10 9v12H36"/></svg>
  <div class="item-text" style="left:776px;top:15px">Multi-lingual Team<br>Translation Summaries<br>Media Analysis</div>
</section>

<section class="band delivery">
  <div class="label" style="top:22px">Content<br>Delivery</div>
  <svg class="icon" style="left:329px;top:25px" width="52" height="50" viewBox="0 0 52 50"><rect x="1" y="1" width="50" height="36" rx="2"/><rect x="5" y="5" width="42" height="26"/><rect x="11" y="10" width="22" height="14"/><path d="M14 15h10M14 19h6M33 20l6 6 2-3 4 4M20 37v6h12v-6M12 48h28"/></svg>
  <svg class="icon" style="left:398px;top:25px" width="52" height="50" viewBox="0 0 52 50"><path d="M1 20L26 2l25 18v28H1z"/><path d="M1 48l19-16h12l19 16M1 20l17 13M51 20L34 33"/><rect x="12" y="8" width="28" height="18" fill="#1e1e1e"/><path d="M18 13h16M18 17h16M18 21h10"/></svg>
  <div class="item-text" style="left:470px;top:36px">APIs Integration</div>
</section>

<div class="end-strip"></div>

<footer class="site-footer">
  <small>Copyright © 2019 Vennatra. All Rights Reserved.</small>
  <div class="social" aria-label="Social links"><span></span><span></span><span></span></div>
</footer>
</body>
</html>
```